institute for female grief councelors needs a design for its facebook group

Each year about 350.000 German women do have a misscarriage while they are pregnant. Their pain and grief is soul deep. Lots of them are stay still in grief even if they have got other children who are healthy and alive. Lots of these women have got difficulty in finally letting go pain, rage and grief. Some are even still in grief after more than twenty or thirty years of having lost their child through misscarriage!!!!

With this facebook group I want to give hope, trust and support as well as helpful advice in coping with this deep soul pain after having lost your child through misscarriage.

The facebook cover shall cause a great curiosity and fascination to the mothers so that they are interested in joining our facebook group.

At our institute women can book a-one-year-training to become a certified "Coach for BirkenFeen" (grief councelor for women who are in deep grief after their misscarriage).

In Germany children who died through misscarriage are named "Sternenkind" (STARCHILD).
Therefore I want to have at least one shing star at the facebook cover symbolizing the still shining soullight of the dead child watching its mother who is still living on earth.

On the left side of the uploaded file you see the planet venus: symbol for mothers / female side of life.
The red sky colour symbolizes the colour of the uterus, the embryo's home before having died through misscarriage.
It ist also possible to include the silhoutte of a mother / several mothers looking up into the red / blue sky to watch the shining soullight of their dead child.

The facebook cover MUST include the following sentence:

Mama, ich lasse mein Licht für dich leuchten

(Mummy, I let my soullight shine for you)

Low design quality

Target Market(s)

German speaking mothers

Industry/Entity Type

coaching

Font styles to use
Script

Colors

Designer to choose colors to be used in the design.

Requirements
Must have
• golden fond writing, at least one shing star, silhouette of one / several mothers (no model typa - normal woman)
Nice to have
• planet venus - red background cover (like uterus colour)
Should not have
• mothers who like like a model or filmstar

```html
<!DOCTYPE html>
<html lang="de">
<head>
<meta charset="utf-8">
<title>Sternenkind Cover</title>
<link href="https://fonts.googleapis.com/css2?family=Kaushan+Script&display=swap" rel="stylesheet">
<style>
  :root {
    --page: #ffffff;
    --sky-red: #e3131f;
    --sky-crimson: #b21640;
    --sky-violet: #7a1fa8;
    --sky-indigo: #3a1fc0;
    --sky-blue: #0a3fd6;
    --venus-light: #e8b24a;
    --venus-mid: #b87420;
    --venus-dark: #6a3a0c;
    --gold-light: #ffe6a0;
    --gold-mid: #d9a441;
    --gold-dark: #8a5a14;
    --glow: #ffffff;
    --glow-halo: #c9a6ff;
  }
  * { margin: 0; padding: 0; box-sizing: border-box; }
  html, body {
    width: 1200px; height: 1200px; overflow: hidden;
    background: var(--page);
  }
  .canvas { position: relative; width: 1200px; height: 1200px; }
  .cover {
    position: absolute; left: 0; top: 376px;
    width: 1200px; height: 447px; overflow: hidden;
    background: linear-gradient(90deg,
      var(--sky-red) 0%, var(--sky-crimson) 30%, var(--sky-violet) 52%,
      var(--sky-indigo) 70%, var(--sky-blue) 100%);
  }
  .sky-texture {
    position: absolute; inset: 0;
    background:
      radial-gradient(ellipse 260px 120px at 150px 20px, rgba(120,0,20,.35), transparent 70%),
      radial-gradient(ellipse 300px 200px at 1050px 120px, rgba(30,80,255,.35), transparent 70%),
      radial-gradient(ellipse 400px 220px at 700px 300px, rgba(60,0,90,.25), transparent 70%);
  }
  .mother-silhouette {
    position: absolute; left: 276px; top: 20px;
    width: 360px; height: 427px;
    border-radius: 48% 52% 10% 10% / 40% 40% 10% 10%;
    background: radial-gradient(ellipse at 50% 40%, rgba(110,10,40,.45), rgba(110,10,40,.15) 60%, transparent 80%);
  }
  .venus {
    position: absolute; left: 0; top: 187px;
    width: 294px; height: 294px; border-radius: 50%;
    background: radial-gradient(circle at 40% 40%, var(--venus-light), var(--venus-mid) 55%, var(--venus-dark) 100%);
  }
  .soul-star {
    position: absolute; left: 744px; top: 2px;
    width: 300px; height: 300px; border-radius: 50%;
    background: radial-gradient(circle,
      var(--glow) 0%, var(--glow) 14%, rgba(230,210,255,.85) 24%,
      rgba(201,166,255,.45) 32%, rgba(160,120,255,.15) 45%, transparent 62%);
  }
  .message {
    position: absolute; left: 340px; top: 214px;
    font-family: "Kaushan Script", cursive;
    font-size: 50px; line-height: 70px; white-space: nowrap;
    background: linear-gradient(180deg, var(--gold-light) 0%, var(--gold-mid) 50%, var(--gold-dark) 100%);
    -webkit-background-clip: text; background-clip: text; color: transparent;
    filter: drop-shadow(2px 3px 2px rgba(40,0,20,.7));
  }
  .message span { display: block; }
</style>
</head>
<body>
<main class="canvas">
  <section class="cover">
    <div class="sky-texture"></div>
    <div class="mother-silhouette" role="img" aria-label="Faint silhouette of a mother looking up to the sky"></div>
    <div class="venus" role="img" aria-label="Planet Venus, golden surface"></div>
    <div class="soul-star" role="img" aria-label="Shining star, the soul light of the star child"></div>
    <h1 class="message">
      <span>Mama,</span>
      <span>ich lasse mein Licht für dich leuchten</span>
    </h1>
  </section>
</main>
</body>
</html>
```